Brellwick Partners, LLC Stationary

Brellwick Partners, LLC is a new financial planning and consulting company. We are looking for designs on business cards, letterhead, envelopes, and anything else that would be useful. Our preference for business card design is two sided. We are looking for a professional and clean look with incorporating the logo and patriotic feel. Thank you to all who participate and good luck!

```html
<!DOCTYPE html>
<html lang="en">
<head>
<meta charset="utf-8">
<title>Brellwick Partners, LLC — Business Card</title>
<link rel="stylesheet" href="https://fonts.googleapis.com/css2?family=Arimo:wght@400;700&display=swap">
<style>
  :root {
    --page-bg: #e9e6e1;
    --navy: #1d3f6e;
    --navy-deep: #15325a;
    --red: #c8202b;
    --red-deep: #8f1a22;
    --white: #ffffff;
    --ink-light: #f2f4f8;
  }
  * { box-sizing: border-box; margin: 0; padding: 0; }
  html, body {
    width: 1200px; height: 950px; overflow: hidden;
    background: var(--page-bg);
    font-family: "Arimo", Arial, sans-serif;
  }
  .sheet {
    width: 1200px; height: 950px;
    display: flex; flex-direction: column; align-items: center; justify-content: center;
    gap: 40px;
  }
  .card {
    position: relative;
    width: 760px; height: 434px;
    overflow: hidden;
    box-shadow: 0 10px 28px rgba(0,0,0,0.22);
  }
  /* Back */
  .card-back {
    background: linear-gradient(135deg, var(--red) 0%, #b31d27 55%, var(--red-deep) 100%);
    color: var(--white);
  }
  .card-back .brand { position: absolute; left: 0; right: 0; top: 150px; justify-content: center; }
  .card-back .brand-name { color: var(--white); }
  .card-back .brand-tagline { color: var(--white); opacity: 0.9; }
  .card-back .back-web {
    position: absolute; right: 150px; bottom: 78px;
    font-size: 20px; letter-spacing: 2px; color: rgba(255,255,255,0.85);
  }
  /* Brand block */
  .brand { display: flex; align-items: center; gap: 16px; }
  .brand-dot { width: 34px; height: 34px; border-radius: 50%; flex: none; }
  .card-back .brand-dot { background: var(--white); }
  .card-front .brand-dot { background: var(--red); }
  .brand-text { display: flex; flex-direction: column; }
  .brand-name { font-size: 38px; font-weight: 700; letter-spacing: 1px; line-height: 1.05; }
  .brand-tagline {
    margin-top: 8px; font-size: 12px; letter-spacing: 2.5px; text-transform: uppercase;
  }
  /* Front */
  .card-front { background: var(--white); }
  .card-front .wave { position: absolute; inset: 0; }
  .card-front .brand { position: absolute; left: 190px; top: 72px; }
  .card-front .brand-name { color: var(--navy); }
  .card-front .brand-tagline { color: var(--red); }
  .holder {
    position: absolute; right: 430px; top: 232px;
    text-align: right; color: var(--white);
    font-size: 19px; line-height: 27px;
  }
  .holder-name { font-size: 22px; font-weight: 700; letter-spacing: 1px; }
  .divider {
    position: absolute; left: 350px; top: 245px; width: 1px; height: 140px;
    background: rgba(255,255,255,0.7);
  }
  .contacts {
    position: absolute; left: 372px; top: 262px;
    list-style: none; color: var(--ink-light); font-size: 19px;
  }
  .contacts li { display: flex; align-items: center; gap: 10px; height: 29px; }
  .contacts svg { width: 17px; height: 17px; flex: none; }
</style>
</head>
<body>
<main class="sheet">

  <section class="card card-back" aria-label="Business card, back">
    <div class="brand">
      <span class="brand-dot"></span>
      <div class="brand-text">
        <span class="brand-name">Brellwick Partners, LLC</span>
        <span class="brand-tagline">Financial Planning and Consulting</span>
      </div>
    </div>
    <p class="back-web">www.brellwick.com</p>
  </section>

  <section class="card card-front" aria-label="Business card, front">
    <svg class="wave" viewBox="0 0 760 434" preserveAspectRatio="none" aria-hidden="true">
      <defs>
        <linearGradient id="navyFill" x1="0" y1="0" x2="1" y2="1">
          <stop offset="0" stop-color="#1f4475"/>
          <stop offset="1" stop-color="#15325a"/>
        </linearGradient>
      </defs>
      <path d="M0 150 C 180 100, 420 205, 760 305 L760 316 C 420 222, 180 118, 0 170 Z" fill="#c8202b"/>
      <path d="M0 182 C 190 128, 420 232, 760 332 L760 434 L0 434 Z" fill="url(#navyFill)"/>
    </svg>

    <div class="brand">
      <span class="brand-dot"></span>
      <div class="brand-text">
        <span class="brand-name">Brellwick Partners, LLC</span>
        <span class="brand-tagline">Financial Planning and Consulting</span>
      </div>
    </div>

    <div class="holder">
      <p class="holder-name">MARCUS HALE</p>
      <p>President</p>
      <p>4127 Linden Crest Road</p>
      <p>Maple Ridge, NY 11020</p>
    </div>

    <div class="divider"></div>

    <ul class="contacts">
      <li>
        <svg viewBox="0 0 20 20" aria-label="Phone"><path fill="#fff" d="M3 6c0-2 2-3 7-3s7 1 7 3v2h-4V6H7v2H3zM5 9h10l2 8H3z"/></svg>
        555 0142 7781
      </li>
      <li>
        <svg viewBox="0 0 20 20" aria-label="Fax"><path fill="#fff" d="M5 2h10v5H5zM2 8h16v7h-3v3H5v-3H2zM7 13v3h6v-3z"/></svg>
        555 0163 2094
      </li>
      <li>
        <svg viewBox="0 0 20 20" aria-label="Email"><path fill="#fff" d="M2 4h16v12H2zM3 5l7 6 7-6z" fill-rule="evenodd"/></svg>
        marcus@brellwick.com
      </li>
      <li>
        <svg viewBox="0 0 20 20" aria-label="Website"><circle cx="10" cy="10" r="8" fill="none" stroke="#fff" stroke-width="2"/><path d="M2 10h16M10 2c-4 4-4 12 0 16M10 2c4 4 4 12 0 16" fill="none" stroke="#fff" stroke-width="1.4"/></svg>
        www.brellwick.com
      </li>
    </ul>
  </section>

</main>
</body>
</html>
```